MBRDC redesign and update stationary bc envelopes.

Stationary, Envelopes, Brochures, Business Card. Need to add second surgeon and two other offices. I need everything to match. I am a oral & maxillofacial surgeon.
Additional surgeon and three office addresses.
Jae Min Park, DMD, MD, INC

3718 Silver Meadow Parkway
El Dorado Hills, CA 95762

642 Lorin Way, Suite 101
Folsom, CA. 95630

2317 Vale Street, Suite 105
Auburn, CA. 95603
Updates

Logo design uploaded. Zapfino Extra/Adobe Garamond/Palatino are fonts used before. Not sure what is on exisiting stationary.

Target Market(s)

Referral dentist and sometimes patients. I am a oral & Maxillofacial surgeon.

Industry/Entity Type

Dental Clinic

Font styles to use
Serif
Script

Requirements
Must have
• Color of existing stationary. Update is possible.
Nice to have
• Conservative/modern
Should not have
• Playful

```html
<!DOCTYPE html>
<html lang="en">
<head>
<meta charset="utf-8">
<title>MBRDC Stationery Set</title>
<link rel="stylesheet" href="https://fonts.googleapis.com/css2?family=Tinos&family=Arimo&family=Open+Sans&display=swap">
<style>
:root{
  --bg:#e4e4e4;
  --paper:#ffffff;
  --brown:#6b4f3f;
  --green:#6f9a23;
  --name-green:#6b8e23;
  --ink:#1d1d1d;
  --body-ink:#4a4a4a;
  --rule:#9a9a9a;
  --hill-sky:#dfe9f1;
  --hill-green:#d9e3a6;
  --hill-gold:#f3ebc2;
  --label:#8a8a8a;
}
*{box-sizing:border-box;margin:0;padding:0}
html,body{width:1200px;height:769px;overflow:hidden}
body{background:var(--bg);position:relative;font-family:"Arimo",Arial,sans-serif;color:var(--ink)}
.sheet{position:absolute;background:var(--paper);box-shadow:0 2px 6px rgba(0,0,0,.25);overflow:hidden}
.band-top{position:absolute;left:0;right:0;top:0;background:var(--brown)}
.band-bottom{position:absolute;left:0;right:0;bottom:0;background:var(--green)}
.serif-name{font-family:"Tinos","Times New Roman",serif;color:var(--name-green);white-space:nowrap}
.line{white-space:nowrap}
.hills{position:absolute;background:radial-gradient(ellipse at 50% 30%,var(--hill-green) 0%,var(--hill-sky) 40%,rgba(243,235,194,.8) 65%,rgba(255,255,255,0) 80%)}
.brand{position:absolute;display:flex;align-items:center;gap:4px;font-family:"Tinos","Times New Roman",serif;color:var(--brown)}
.brand .dot{border-radius:50%;background:var(--hill-green)}
.icon{display:inline-block;vertical-align:-1px;margin-right:2px}
.dotsep{display:inline-block;width:4px;height:4px;border-radius:50%;background:var(--green);margin:0 3px;vertical-align:1px}

/* Letterhead */
.letterhead{left:86px;top:100px;width:438px;height:560px}
.letterhead .band-top{height:7px}
.letterhead .band-bottom{height:8px}
.letterhead .brand{left:44px;top:40px;font-size:22px}
.letterhead .brand .dot{width:16px;height:16px}
.lh-contact{position:absolute;left:257px;top:18px;border-left:1px solid var(--rule);height:68px}
.lh-contact-inner{position:absolute;left:10px;top:-3px;font-size:6.4px;line-height:8.2px}
.lh-contact .serif-name{font-size:8px;line-height:10px}
.letter{position:absolute;left:41px;top:101px;width:356px;font-family:"Open Sans",Arial,sans-serif;color:var(--body-ink);font-size:7.1px}
.letter p{line-height:12.6px;text-align:justify}
.letter .date{position:absolute;top:0}
.letter .recipient{position:absolute;top:17px;line-height:8.5px;text-align:left}
.letter .salute{position:absolute;top:66px}
.letter .body{position:absolute;top:89px;width:356px}
.letter .body p + p{margin-top:12.6px}
.letter .close{position:absolute;top:280px}
.signature{position:absolute;left:41px;top:399px;width:100px;height:11px;background:linear-gradient(90deg,rgba(80,80,80,.35),rgba(80,80,80,.1))}
.signer{position:absolute;left:41px;top:415px;font-family:"Open Sans",Arial,sans-serif;color:var(--body-ink)}
.signer .who{font-size:8.8px}
.signer .role{font-size:7.1px;margin-top:4px}
.letterhead .hills{left:224px;top:448px;width:240px;height:104px}
.lh-footer{position:absolute;left:0;right:0;top:500px;text-align:center;font-size:7.6px;line-height:11px}
.lh-footer .services{margin-top:5px;font-size:7.8px;line-height:10px}

/* Envelope */
.label{position:absolute;left:814px;top:124px;font-size:18px;color:var(--label);font-family:"Arimo",Arial,sans-serif}
.envelope{left:596px;top:171px;width:508px;height:230px}
.envelope .band-top{height:8px}
.envelope .band-bottom{height:7px}
.envelope .hills{left:212px;top:88px;width:300px;height:138px}
.envelope .brand{left:12px;top:58px;font-size:17px}
.envelope .brand .dot{width:12px;height:12px}
.env-contact{position:absolute;left:100px;top:17px;font-size:6.5px;line-height:8.3px}
.env-contact .serif-name{font-size:8px;line-height:11px}
.env-contact .addr{margin-top:4px;line-height:10.6px}
.env-services{position:absolute;left:0;width:232px;top:106px;text-align:center;font-size:6.6px;line-height:8.3px}
.env-web{position:absolute;left:29px;top:135px;font-family:"Tinos","Times New Roman",serif;color:var(--name-green);font-size:9.5px;letter-spacing:1.6px}

/* Business cards */
.card{top:487px;width:234px;height:137px}
.card .band-top{height:3px}
.card .band-bottom{height:4px}
.card-front{left:607px}
.card-front .brand{left:128px;top:36px;font-size:17px}
.card-front .brand .dot{width:12px;height:12px}
.card-front .hills{left:120px;top:6px;width:104px;height:34px;opacity:.8}
.cf-names{position:absolute;left:11px;top:18px;font-size:5.6px;line-height:8.4px}
.cf-names .serif-name{font-size:7.7px;line-height:10px}
.cf-addr{position:absolute;left:11px;top:75px;font-family:"Open Sans",Arial,sans-serif;font-size:5.5px;line-height:8.8px}
.cf-addr .gap{margin-top:1px}
.cf-contact{position:absolute;right:10px;top:104px;text-align:right;font-family:"Open Sans",Arial,sans-serif;font-size:5.6px;line-height:8.4px}
.card-back{left:861px}
.card-back .brand{left:16px;top:18px;font-size:22px}
.card-back .brand .dot{width:15px;height:15px}
.card-back .hills{left:80px;top:44px;width:156px;height:92px}
.cb-services{position:absolute;left:15px;top:64px;list-style:none;font-family:"Open Sans",Arial,sans-serif;font-size:5.6px;line-height:8.6px}
.cb-services li::before{content:"";display:inline-block;width:3.5px;height:3.5px;border-radius:50%;background:var(--green);margin-right:3px;vertical-align:0.5px}
</style>
</head>
<body>

<!-- Letterhead -->
<section class="sheet letterhead">
  <div class="band-top"></div>
  <div class="brand"><span class="dot"></span><span>MBRDC</span></div>
  <div class="lh-contact">
    <div class="lh-contact-inner">
      <div class="serif-name">Daniel R. Whitford,DDS,Inc.</div>
      <div class="line">Diplomate of the American Board of</div>
      <div class="line">Oral &amp; Maxillofacial Surgery</div>
      <div class="serif-name" style="margin-top:2px">Jae Min Park, DMD, MD, INC</div>
      <div class="line">Dental Implant and Oral Surgery</div>
      <div class="line" style="margin-top:3px">
        <svg class="icon" width="6" height="6" viewBox="0 0 10 10"><path d="M2 1l2 2-1 1.5c.7 1.3 1.7 2.3 3 3L7.5 6l2 2-1.5 1.5C4.5 9 1 5.5.5 2.5z" fill="var(--green)"/></svg>916.555.0142
        <svg class="icon" style="margin-left:3px" width="6" height="6" viewBox="0 0 10 10"><rect x="2" y="0.5" width="6" height="3" fill="var(--green)"/><rect x="0.5" y="4" width="9" height="4" fill="var(--green)"/><rect x="2.5" y="7" width="5" height="2.5" fill="var(--green)"/></svg>916.555.0187
      </div>
      <div class="line"><svg class="icon" width="6" height="5" viewBox="0 0 10 8"><rect x="0.5" y="0.5" width="9" height="7" fill="var(--green)"/><path d="M.5.5L5 4.5 9.5.5" stroke="#fff" fill="none"/></svg>drwhitford@meadowbrookoralsurgery.com</div>
      <div class="line"><svg class="icon" width="6" height="6" viewBox="0 0 10 10"><circle cx="5" cy="5" r="4.3" fill="none" stroke="var(--green)"/><path d="M.7 5h8.6M5 .7c-2.4 2.5-2.4 6.1 0 8.6M5 .7c2.4 2.5 2.4 6.1 0 8.6" stroke="var(--green)" fill="none" stroke-width=".8"/></svg>www.meadowbrookoralsurgery.com</div>
    </div>
  </div>

  <div class="letter">
    <p class="date">Issuing Date: May 5, 2018</p>
    <p class="recipient">Name Of Employee Mr. XYZABC<br>Address of Employee<br>Address Line 2 etc..</p>
    <p class="salute">Dear Mr.XYZABC</p>
    <div class="body">
      <p>Lorem Ipsum has been the industry's standard dummy text ever since the 1500s, when an unknown printer took a galley of type and scrambled it to make a type specimen book. It has survived not only five centuries, but also the leap into electronic typesetting, remaining essentially unchanged. It was popularised in the 1960s with the release of Letraset sheets containing Lorem Ipsum passages, and more recently with desktop publishing software like Aldus PageMaker including versions of Lorem Ipsum.</p>
      <p>Lorem Ipsum is simply dummy text of the printing and typesetting industry. Lorem Ipsum has been the industry's standard dummy text ever since the 1500s, when an unknown printer took a galley of type and scrambled it to make a type specimen book.</p>
      <p>It has survived not only five centuries, but also the leap into electronic typesetting, remaining essentially unchanged. It was popularised in the 1960s with the release of Letraset sheets containing Lorem IpsumIpsum passages.</p>
    </div>
    <p class="close">Yours Sincerely</p>
  </div>
  <div class="signature" role="img" aria-label="Handwritten signature"></div>
  <div class="signer">
    <div class="who">Marcus Ellison</div>
    <div class="role">Managing Director</div>
  </div>

  <div class="hills" role="img" aria-label="Soft illustration of rolling foothills"></div>
  <div class="lh-footer">
    <div>642 Lorin Way, Suite 101 , Folsom, CA. 95630 | 2317 Vale Street, Suite 105, Auburn, CA. 95603</div>
    <div>3718 Silver Meadow Parkway, El Dorado Hills, CA 95762</div>
    <div class="services">Dentoalveolar Surgery<span class="dotsep"></span>Dental Implant Surgery<span class="dotsep"></span>Orthognathic Surgery<span class="dotsep"></span>Facial Trauma Surgery<br>Preprosthetic and Reconstructive Surgery<span class="dotsep"></span>TMJ Disorders and Surgery<span class="dotsep"></span>Obstructive Sleep Apnea Surgery</div>
  </div>
  <div class="band-bottom"></div>
</section>

<!-- Envelope -->
<div class="label">Envelope</div>
<section class="sheet envelope">
  <div class="band-top"></div>
  <div class="hills" role="img" aria-label="Soft illustration of rolling foothills"></div>
  <div class="brand"><span class="dot"></span><span>MBRDC</span></div>
  <div class="env-contact">
    <div class="serif-name">Daniel R. Whitford,DDS,Inc.</div>
    <div class="line">Diplomate of the American Board of</div>
    <div class="line">Oral &amp; Maxillofacial Surgery</div>
    <div class="serif-name" style="margin-top:3px">Jae Min Park, DMD, MD, INC</div>
    <div class="line">Dental Implant and Oral Surgery</div>
    <div class="addr">3718 Silver Meadow Parkway, El Dorado Hills, CA 95762<br>642 Lorin Way, Suite 101 , Folsom, CA. 95630<br>2317 Vale Street, Suite 105, Auburn, CA. 95603</div>
  </div>
  <div class="env-services">Dentoalveolar Surgery<span class="dotsep"></span>Dental Implant Surgery<span class="dotsep"></span>Orthognathic Surgery<br>Facial Trauma Surgery<span class="dotsep"></span>Preprosthetic and Reconstructive Surgery<br>TMJ Disorders and Surgery<span class="dotsep"></span>Obstructive Sleep Apnea Surgery</div>
  <div class="env-web">www.meadowbrookoralsurgery.com</div>
  <div class="band-bottom"></div>
</section>

<!-- Business card front -->
<section class="sheet card card-front">
  <div class="band-top"></div>
  <div class="hills" role="img" aria-label="Soft illustration of rolling foothills"></div>
  <div class="brand"><span class="dot"></span><span>MBRDC</span></div>
  <div class="cf-names">
    <div class="serif-name">Daniel R. Whitford,DDS,Inc.</div>
    <div class="line">Diplomate of the American Board of</div>
    <div class="line">Oral &amp; Maxillofacial Surgery</div>
    <div class="serif-name" style="margin-top:3px">Jae Min Park, DMD, MD, INC</div>
    <div class="line">Dental Implant and Oral Surgery</div>
  </div>
  <div class="cf-addr">
    <div>3718 Silver Meadow Parkway</div>
    <div>El Dorado Hills, CA 95762</div>
    <div class="gap">2317 Vale Street, Suite 105</div>
    <div>Auburn, CA. 95603</div>
    <div class="gap">642 Lorin Way, Suite 101</div>
    <div>Folsom, CA. 95630</div>
  </div>
  <div class="cf-contact">
    <div>916.555.0142 <svg class="icon" width="6" height="6" viewBox="0 0 10 10"><rect x="2" y="0.5" width="6" height="3" fill="var(--green)"/><rect x="0.5" y="4" width="9" height="4" fill="var(--green)"/><rect x="2.5" y="7" width="5" height="2.5" fill="var(--green)"/></svg>916.555.0187 <svg class="icon" width="6" height="6" viewBox="0 0 10 10"><path d="M2 1l2 2-1 1.5c.7 1.3 1.7 2.3 3 3L7.5 6l2 2-1.5 1.5C4.5 9 1 5.5.5 2.5z" fill="var(--green)"/></svg></div>
    <div>drwhitford@meadowbrookoralsurgery.com <svg class="icon" width="6" height="5" viewBox="0 0 10 8"><rect x="0.5" y="0.5" width="9" height="7" fill="var(--green)"/><path d="M.5.5L5 4.5 9.5.5" stroke="#fff" fill="none"/></svg></div>
    <div>www.meadowbrookoralsurgery.com <svg class="icon" width="6" height="6" viewBox="0 0 10 10"><circle cx="5" cy="5" r="4.3" fill="none" stroke="var(--green)"/><path d="M.7 5h8.6M5 .7c-2.4 2.5-2.4 6.1 0 8.6M5 .7c2.4 2.5 2.4 6.1 0 8.6" stroke="var(--green)" fill="none" stroke-width=".8"/></svg></div>
  </div>
  <div class="band-bottom"></div>
</section>

<!-- Business card back -->
<section class="sheet card card-back">
  <div class="band-top"></div>
  <div class="hills" role="img" aria-label="Soft illustration of rolling foothills"></div>
  <div class="brand"><span class="dot"></span><span>MBRDC</span></div>
  <ul class="cb-services">
    <li>Dentoalveolar Surgery</li>
    <li>Dental Implant Surgery</li>
    <li>Orthognathic Surgery</li>
    <li>Facial Trauma Surgery</li>
    <li>Preprosthetic and Reconstructive Surgery</li>
    <li>TMJ Disorders and Surgery</li>
    <li>Obstructive Sleep Apnea Surgery</li>
  </ul>
  <div class="band-bottom"></div>
</section>

</body>
</html>
```